Business card for Crestline Bathrooms

Please design a business card for our bathroom renovation business. You can use my existing logo, but if you have an idea to modernize it, I would like to see it. Please see attached files first. I would like to use the blue and the orange theme. I like the concept of using the shower head in the logo. Please find following a design (or two) that I have been trying to create with my limited resources. That design was for a sign, but I was going to adopt it and use it as a business card as well. I like the concept of the water splash but I don’t think it “flows” nicely together with the logo. Another thought is that maybe creating the logo out of water splash could work and have a dramatic effect (like the water text and the butterfly picture attached with similar background instead of white). If the above doesn’t work I would like to see a modern simplified design. One of the attached files named as the unwanted business card has all the details that I want included in the business card. Please note that it is two sided.
Updates

I am very thankful for the designs that I have received, but they are very similar and only a couple of attempts to do something with the water splash as per my original brief. Modernizing the logo and having it made out of out of water splash with the orange as color accent could work and have a dramatic effect (like the water text and the butterfly picture attached with similar background instead of white). Please do not use the butterfly itself! This is just an example that images can be created out of water splash.

Contact Information for Business Card

all the details are on the unwonted business card file included

Colors
3176b5

Requirements
Nice to have
• Copied from the brief:
• ... maybe creating the logo out of water splash could work and have a dramatic effect (like the water text and the butterfly picture attached with similar background instead of white). Please do not use the butterfly itself!
Should not have
• I am getting designs with a butterfly. The butterfly picture was an example of creating something from a water splash. The butterfly itself has no association with anything other than the concept of creating a logo out of water splash. Sorry, I thought I was clear in the brief.

```html
<!DOCTYPE html>
<html lang="en">
<head>
<meta charset="utf-8">
<title>Crestline Bathrooms – Business Card</title>
<link href="https://fonts.googleapis.com/css2?family=Roboto:wght@400&family=Comic+Neue:wght@400&display=swap" rel="stylesheet">
<style>
  :root {
    --navy: #03406b;
    --coral: #ea776b;
    --white: #ffffff;
    --paper: #e6e6e6;
    --ink: #4a4a4a;
    --badge: #6b6b6b;
  }
  * { margin: 0; padding: 0; box-sizing: border-box; }
  html, body { width: 1200px; height: 960px; overflow: hidden; }
  body {
    position: relative;
    background: var(--paper);
    font-family: "Roboto", Arial, sans-serif;
  }
  .card {
    position: absolute;
    overflow: hidden;
    box-shadow: 2px 3px 4px rgba(0,0,0,0.35);
  }
  /* Front */
  .card-front {
    left: 314px; top: 113px; width: 602px; height: 342px;
    background: var(--navy);
  }
  .front-art { position: absolute; inset: 0; }
  .holder-name {
    position: absolute; left: 43px; top: 48px;
    font-family: "Comic Neue", "Comic Sans MS", cursive;
    font-size: 25px; color: var(--coral); letter-spacing: 0.5px;
  }
  .contact-list { position: absolute; left: 43px; top: 179px; list-style: none; }
  .contact-item {
    position: relative; padding-left: 22px;
    color: var(--white); font-size: 14.5px; line-height: 19.5px;
  }
  .contact-item + .contact-item { margin-top: 0; }
  .contact-item.gap { margin-top: 8px; }
  .contact-icon {
    position: absolute; left: 0; top: 3px; width: 13px; height: 13px;
  }
  /* Back */
  .card-back {
    left: 311px; top: 472px; width: 600px; height: 343px;
    background: var(--white);
  }
  .brand-name {
    position: absolute; left: 48px; top: 118px; width: 224px;
    display: flex; align-items: center; gap: 10px;
    color: var(--navy); font-size: 31px; line-height: 36px;
  }
  .brand-dot {
    flex: none; width: 14px; height: 14px; border-radius: 50%;
    background: var(--navy);
  }
  .divider {
    position: absolute; left: 304px; top: 48px; width: 2px; height: 252px;
    background: var(--coral);
  }
  .service-list { position: absolute; left: 341px; top: 45px; list-style: none; }
  .service-item {
    position: relative; padding-left: 14px;
    color: var(--ink); font-size: 14.5px; line-height: 19px;
    margin-bottom: 19px;
  }
  .service-item::before {
    content: ""; position: absolute; left: 0; top: 6px;
    width: 5px; height: 5px; border-radius: 50%; background: var(--navy);
  }
  .memberships {
    position: absolute; left: 340px; top: 266px;
    display: flex; align-items: center; gap: 16px;
  }
  .badge-square { width: 32px; height: 34px; border-radius: 4px; background: var(--badge); }
  .badge-rule { width: 1px; height: 34px; background: var(--badge); }
  .badge-wide { width: 117px; height: 26px; background: var(--badge); }
</style>
</head>
<body>

<section class="card card-front">
  <svg class="front-art" width="602" height="342" viewBox="0 0 602 342">
    <path role="img" aria-label="Large white shower-head emblem sweeping over a coral panel"
          fill="var(--coral)"
          d="M300,0 C268,40 268,100 312,142 C382,202 398,262 330,300 C290,324 245,335 225,342 L602,342 L602,0 Z"/>
  </svg>

  <h1 class="holder-name">Daniel Harwick</h1>

  <ul class="contact-list">
    <li class="contact-item">
      <svg class="contact-icon" viewBox="0 0 12 12"><path fill="var(--coral)" d="M6 0a4 4 0 0 0-4 4c0 3 4 8 4 8s4-5 4-8a4 4 0 0 0-4-4zm0 5.5A1.5 1.5 0 1 1 6 2.5a1.5 1.5 0 0 1 0 3z"/></svg>
      PO Box 48<br>Kelmscott Vale 2734
    </li>
    <li class="contact-item gap">
      <svg class="contact-icon" viewBox="0 0 12 12"><path fill="var(--coral)" d="M2.5 0.5l2 2.5-1.2 1.5c.8 1.7 2.2 3.1 3.9 3.9L8.7 7.2l2.5 2-.9 2.3C5 11.3.7 7 .4 1.4z"/></svg>
      0400 318 572
    </li>
    <li class="contact-item">
      <svg class="contact-icon" viewBox="0 0 12 12"><rect x="3" y="0" width="6" height="12" rx="1.2" fill="none" stroke="var(--coral)" stroke-width="1.4"/><rect x="5" y="9.5" width="2" height="1" fill="var(--coral)"/></svg>
      6200 4417
    </li>
    <li class="contact-item">
      <svg class="contact-icon" viewBox="0 0 12 12"><rect x="0.5" y="2.5" width="11" height="8" fill="var(--coral)"/><path d="M0.5 2.5l5.5 4 5.5-4" fill="none" stroke="var(--navy)" stroke-width="1"/></svg>
      daniel@crestlinebathrooms.com.au
    </li>
    <li class="contact-item">
      <svg class="contact-icon" viewBox="0 0 12 12"><circle cx="6" cy="6" r="5.5" fill="var(--coral)"/><path d="M3 4c1 0 2 1 1.5 2S5 8 6 9M7 2.5c-.5 1 .5 1.5 1.5 1.5s1 1.5.5 2.5" fill="none" stroke="var(--navy)" stroke-width="0.9"/></svg>
      crestlinebathrooms.com.au
    </li>
  </ul>
</section>

<section class="card card-back">
  <div class="brand-name"><span class="brand-dot"></span><span>Crestline Bathrooms</span></div>

  <div class="divider"></div>

  <ul class="service-list">
    <li class="service-item">Complete Bathroom<br>Renovations &amp; Remodelling</li>
    <li class="service-item">Highly Skilled &amp;<br>Qualified Tradespeople</li>
    <li class="service-item">Professional Service From<br>Concept To Completion</li>
    <li class="service-item">All Work Guaranteed</li>
  </ul>

  <div class="memberships" aria-label="Industry memberships">
    <div class="badge-square"></div>
    <div class="badge-rule"></div>
    <div class="badge-wide"></div>
  </div>
</section>

</body>
</html>
```